Veltrano.co - Polar Expeditions Specialists

We need a modern, visually striking business card for Veltrano.co, a company specialized in selling expedition cruises to the most remote regions on Earth, with a focus on the Arctic and Antarctica. The design should instantly communicate that the cardholder is an expert in polar travel. Use clean, premium aesthetics with cool tones like icy blue and white, possibly incorporating polar imagery (ice, glaciers, penguins, etc.)

Attached the logo

Contact Information for Business Card

Feels high-end and trustworthy.. Visually memorable — encourages people to keep it

Colors
0054AA
0677BA
7BADD7
CADEEF
E8F1F8

Requirements
Must have
• ice, glaciers, penguins, montains
Nice to have
• modern, transparente,

```html
<!DOCTYPE html>
<html lang="en">
<head>
<meta charset="utf-8">
<title>Veltrano.co Business Card</title>
<link href="https://fonts.googleapis.com/css2?family=Poppins:wght@600;800&family=Montserrat:wght@400;700&display=swap" rel="stylesheet">
<style>
  :root{
    --deep-blue:#0054AA;
    --brand-blue:#2E78BE;
    --sky-blue:#7BADD7;
    --ice-blue:#CADEEF;
    --frost:#E8F1F8;
    --white:#FFFFFF;
    --ink:#3A3F47;
    --stage:#E4E6E9;
  }
  *{box-sizing:border-box;margin:0;padding:0}
  html,body{width:1200px;height:900px;overflow:hidden;background:var(--stage)}
  .canvas{position:relative;width:1200px;height:900px}
  .card{position:absolute;left:300px;width:600px;height:343px;border-radius:26px;overflow:hidden;
    box-shadow:0 6px 18px rgba(0,0,0,.12)}
  .card--back{top:60px;background:var(--brand-blue)}
  .card--front{top:470px;background:var(--white)}

  .back__photo{position:absolute;inset:0;
    background:radial-gradient(ellipse at 55% 45%, #9CC1E4 0%, #6FA2D3 40%, #4F8BC8 75%, #4A86C4 100%)}
  .lockup{position:absolute;display:flex;flex-direction:column;align-items:flex-start}
  .lockup__name{display:flex;align-items:center;gap:12px;font-family:'Poppins',sans-serif;font-weight:800;line-height:1;letter-spacing:.5px}
  .lockup__dot{border-radius:50%;flex:none}
  .lockup__tagline{font-family:'Poppins',sans-serif;font-weight:600;letter-spacing:.3px}

  .card--back .lockup{left:110px;top:120px}
  .card--back .lockup__name{color:var(--white);font-size:62px}
  .card--back .lockup__dot{width:46px;height:46px;background:var(--white)}
  .card--back .lockup__tagline{color:var(--white);font-size:17px;margin:8px 0 0 58px}

  .card--front .lockup{left:150px;top:58px}
  .card--front .lockup__name{color:var(--brand-blue);font-size:56px}
  .card--front .lockup__dot{width:42px;height:42px;background:var(--brand-blue)}
  .card--front .lockup__tagline{color:var(--brand-blue);font-size:15px;margin:6px 0 0 54px}

  .holder{position:absolute;left:120px;top:185px;text-align:right;width:170px}
  .holder__name{font-family:'Montserrat',sans-serif;font-weight:700;font-size:22px;color:var(--brand-blue);letter-spacing:1px}
  .holder__role{font-family:'Montserrat',sans-serif;font-weight:400;font-size:15px;color:var(--ink);margin-top:2px}
  .divider{position:absolute;left:306px;top:178px;width:1px;height:68px;background:var(--brand-blue)}
  .contacts{position:absolute;left:322px;top:176px;list-style:none}
  .contacts li{display:flex;align-items:center;gap:8px;font-family:'Montserrat',sans-serif;font-size:13.5px;color:var(--ink);height:23px}
  .contacts svg{width:12px;height:12px;fill:var(--brand-blue);flex:none}

  .address-band{position:absolute;left:0;right:0;top:268px;height:42px;background:var(--brand-blue);
    display:flex;align-items:center;justify-content:center;
    font-family:'Montserrat',sans-serif;font-size:14px;color:var(--white);letter-spacing:.8px}
</style>
</head>
<body>
<main class="canvas">
  <section class="card card--back">
    <div class="back__photo" role="img" aria-label="Polar bear walking on snowy ice, tinted blue"></div>
    <div class="lockup">
      <div class="lockup__name"><span class="lockup__dot"></span>Veltrano.co</div>
      <div class="lockup__tagline">Polar Expeditions Specialists</div>
    </div>
  </section>

  <section class="card card--front">
    <div class="lockup">
      <div class="lockup__name"><span class="lockup__dot"></span>Veltrano.co</div>
      <div class="lockup__tagline">Polar Expeditions Specialists</div>
    </div>
    <div class="holder">
      <div class="holder__name">DANIEL HART</div>
      <div class="holder__role">CEO / Founder</div>
    </div>
    <div class="divider"></div>
    <ul class="contacts">
      <li><svg viewBox="0 0 24 24"><path d="M6.6 10.8a15 15 0 0 0 6.6 6.6l2.2-2.2c.3-.3.7-.4 1-.2 1.1.4 2.3.6 3.6.6.6 0 1 .4 1 1V20c0 .6-.4 1-1 1A17 17 0 0 1 3 4c0-.6.4-1 1-1h3.5c.6 0 1 .4 1 1 0 1.3.2 2.5.6 3.6.1.3 0 .7-.2 1z"/></svg>+43 660 21 48 375</li>
      <li><svg viewBox="0 0 24 24"><path d="M2 5h20v14H2zm2 2v.5l8 5 8-5V7l-8 5z"/></svg>daniel.hart@veltrano.co</li>
      <li><svg viewBox="0 0 24 24"><circle cx="12" cy="12" r="10"/></svg>www.veltrano.co</li>
    </ul>
    <div class="address-band">P.O. Box 3120 Harbour Lane Nordvik NV 4127</div>
  </section>
</main>
</body>
</html>
```